Kelvaro.ch is looking for business card letterhead and envelope C5 with WOW effect

We need a strong business card for our company Kelvaro.ch, logo is available. You want a black or dark background on which the logo Stark r% 26 # 252; appears. Letterhead and envelope in C5 format should be in a similar design, but does not have to be We need a strong business card for our company Kelvaro.ch, logo is available. A black or dark background is desired, on which the logo Stark comes across. The letterhead and the envelope in C5 format should have a similar design.

Target Market(s)

Private customers as well as entrepreneurs

Contact Information for Business Card

E-mail: info@kelvaro-example.ch
Web.www.Kelvaro-example.ch
Tel: +41 ( 0 ) 79 482 6037
Adresse:
Lindenweg 14
9406 Tarnbach

Hier kann man Icons verwenden für Email,Tel und Adressse

Font styles to use
Other font styles liked:
• Dubai,bold

Colors

Designer to choose colors to be used in the design.

Requirements
Must have
• WOW effect
Nice to have
• R% 26 # 252; back business card with our service listings. - VEHICLE LABELING - SHOP WINDOW LABELING - STICKERS AND MUCH MORE ... in red color

```html
<!DOCTYPE html>
<html lang="en">
<head>
<meta charset="utf-8">
<title>Kelvaro.ch – Business Card</title>
<link rel="stylesheet" href="https://fonts.googleapis.com/css2?family=Ubuntu:wght@300;400;500;700&display=swap">
<style>
  :root {
    --backdrop: #4a443e;
    --card: #1b1b1c;
    --card-edge: #262627;
    --white: #ffffff;
    --soft: #e6e6e6;
    --accent: #fcc722;
    --accent-deep: #f2b705;
    --service-red: #e3141b;
  }
  * { box-sizing: border-box; margin: 0; padding: 0; }
  html, body { width: 1200px; height: 930px; overflow: hidden; }
  body {
    background: var(--backdrop);
    font-family: "Ubuntu", sans-serif;
    display: flex;
    flex-direction: column;
    align-items: center;
    justify-content: center;
    gap: 40px;
  }
  .card {
    position: relative;
    width: 640px;
    height: 400px;
    border-radius: 22px;
    background: linear-gradient(135deg, var(--card-edge) 0%, var(--card) 60%, #141415 100%);
    color: var(--white);
    overflow: hidden;
  }
  .brand {
    position: absolute;
    display: flex;
    align-items: center;
    gap: 12px;
    font-weight: 700;
    text-transform: uppercase;
    color: var(--white);
    letter-spacing: 1px;
    white-space: nowrap;
  }
  .brand__mark {
    width: 20px;
    height: 20px;
    background: var(--accent);
    flex: none;
  }
  .pattern-area {
    position: absolute;
    border-radius: 40px;
    background: radial-gradient(ellipse at 45% 45%, var(--accent) 0%, var(--accent-deep) 45%, rgba(242,183,5,0.35) 75%, rgba(242,183,5,0) 100%);
  }

  /* Service side */
  .card--services .pattern-area {
    left: 70px;
    top: 130px;
    width: 200px;
    height: 150px;
  }
  .card--services .brand {
    left: 300px;
    top: 120px;
    font-size: 40px;
  }
  .services {
    position: absolute;
    right: 50px;
    top: 190px;
    list-style: none;
    font-weight: 300;
    font-size: 16px;
    text-transform: uppercase;
    line-height: 1.55;
    color: var(--soft);
    text-align: right;
  }
  .services li { display: flex; align-items: center; justify-content: flex-end; gap: 10px; }
  .services li::after {
    content: "";
    width: 9px;
    height: 9px;
    border: 2px solid var(--service-red);
    border-radius: 50%;
  }

  /* Contact side */
  .card--contact .pattern-area {
    left: 360px;
    top: 30px;
    width: 250px;
    height: 290px;
  }
  .card--contact .brand {
    left: 40px;
    top: 44px;
    font-size: 38px;
  }
  .person {
    position: absolute;
    left: 60px;
    top: 185px;
  }
  .person__name {
    font-weight: 700;
    font-size: 26px;
    letter-spacing: 2px;
    text-transform: uppercase;
  }
  .person__name .surname { color: var(--accent); }
  .person__role { font-size: 16px; margin-top: 2px; }
  .divider {
    width: 40px;
    height: 2px;
    background: var(--accent);
    margin: 16px 0 12px;
  }
  .contact { list-style: none; font-size: 17px; line-height: 1.6; }
  .contact li { display: flex; align-items: center; gap: 12px; }
  .contact svg { width: 15px; height: 15px; flex: none; }
  .contact .address { margin-top: 2px; }
</style>
</head>
<body>

  <section class="card card--services" aria-label="Card back with services">
    <div class="pattern-area" role="img" aria-label="Yellow hexagon cluster decoration"></div>
    <div class="brand"><span class="brand__mark"></span>Kelvaro.ch</div>
    <ul class="services">
      <li>Vehicle labeling</li>
      <li>Shop window labeling</li>
      <li>Stickers and much more</li>
    </ul>
  </section>

  <section class="card card--contact" aria-label="Card front with contact details">
    <div class="pattern-area" role="img" aria-label="Large yellow hexagon cluster decoration"></div>
    <div class="brand"><span class="brand__mark"></span>Kelvaro.ch</div>
    <div class="person">
      <h1 class="person__name">Jonas <span class="surname">Brenner</span></h1>
      <p class="person__role">Director</p>
      <div class="divider"></div>
      <ul class="contact">
        <li>
          <svg viewBox="0 0 16 16" aria-hidden="true"><path d="M3 1.5l3 .5 1 3.5-2 1.2a9 9 0 0 0 4.3 4.3l1.2-2 3.5 1 .5 3c-6.5 1-12-4.5-11.5-11.5z" fill="var(--accent)"/></svg>
          +41 ( 0 ) 79 482 6037
        </li>
        <li>
          <svg viewBox="0 0 16 16" aria-hidden="true"><rect x="1.5" y="3.5" width="13" height="9" fill="none" stroke="var(--accent)" stroke-width="1.5"/><path d="M1.5 3.5L8 9l6.5-5.5" fill="none" stroke="var(--accent)" stroke-width="1.5"/></svg>
          info@kelvaro-example.ch
        </li>
        <li>
          <svg viewBox="0 0 16 16" aria-hidden="true"><circle cx="8" cy="8" r="6.5" fill="none" stroke="var(--accent)" stroke-width="1.5"/><ellipse cx="8" cy="8" rx="2.8" ry="6.5" fill="none" stroke="var(--accent)" stroke-width="1.2"/><path d="M1.5 8h13" stroke="var(--accent)" stroke-width="1.2"/></svg>
          www.Kelvaro-example.ch
        </li>
        <li class="address">Lindenweg 14 9406 Tarnbach</li>
      </ul>
    </div>
  </section>

</body>
</html>
```